Brookvale Building Company - advertisement poster

I am looking to print some canvas signs to advertise my general contracting company, Brookvale Building Company. The sign will measure 6' long x 3' high so the size should match that ratio. I already have a logo icon, which is the Letter 'B' and some trees that I would like to incorporate, see attached. I would also like the to have the following information listed:
1) phone number: 831-555-0172
2) email: brookvalebuildingcompany@mailnest.example
3) website: brookvalebuildingcompany.example
4) Lic#4826130
5) I want to use this text: "BUILD WITH THE B-CREW!"

The ad should be relatively simple and clean. Black and Green are my company colors. I am open to creative ideas!

Target Market(s)

People looking to renovate their homes

Industry/Entity Type

Construction

Colors
59FF00
82FF00
B8FF75
E3FFCB
F4FFEA

Requirements
Must have
• Must have my company logo
Should not have
• No photos or complex graphics

```html
<!DOCTYPE html>
<html lang="en">
<head>
<meta charset="utf-8">
<title>Brookvale Building Company – Sign</title>
<link rel="stylesheet" href="https://fonts.googleapis.com/css2?family=Fira+Sans+Condensed:wght@700&family=Outfit:wght@400;600&display=swap">
<style>
  :root {
    --charcoal: #20261f;
    --leaf: #7dc242;
    --leaf-deep: #6ab245;
    --lime-line: #c5e88a;
    --cream: #e8f5cf;
    --white: #ffffff;
    --slate: #3e4a38;
  }
  html, body { margin: 0; padding: 0; overflow: hidden; background: var(--charcoal); }
  .sign {
    position: relative;
    width: 1200px;
    height: 600px;
    overflow: hidden;
    background: var(--leaf);
    font-family: "Outfit", sans-serif;
  }
  .sign__bands { position: absolute; inset: 0; }
  .brand__mark {
    position: absolute;
    left: 245px;
    top: 148px;
    width: 150px;
    height: 150px;
    border-radius: 50%;
    background: var(--leaf-deep);
  }
  .brand {
    position: absolute;
    left: 60px;
    top: 305px;
    width: 520px;
    text-align: center;
    color: var(--white);
    font-family: "Outfit", sans-serif;
    font-weight: 600;
    line-height: 1;
  }
  .brand__name { font-size: 82px; letter-spacing: 2px; text-transform: uppercase; }
  .brand__line { margin-top: 8px; font-size: 29px; letter-spacing: 13px; text-transform: uppercase; margin-right: -13px; }
  .pitch {
    position: absolute;
    left: 620px;
    width: 540px;
    text-align: center;
    margin: 0;
  }
  .pitch__headline {
    top: 132px;
    font-family: "Fira Sans Condensed", sans-serif;
    font-weight: 700;
    font-size: 53px;
    line-height: 1.1;
    color: var(--cream);
  }
  .pitch__phone {
    top: 243px;
    font-family: "Outfit", sans-serif;
    font-weight: 400;
    font-size: 36px;
    color: var(--leaf);
  }
  .pitch__email, .pitch__web {
    font-size: 15.5px;
    color: var(--white);
    letter-spacing: 0.3px;
  }
  .pitch__email { top: 295px; }
  .pitch__web { top: 324px; }
  .license {
    position: absolute;
    right: 30px;
    bottom: 22px;
    font-size: 24px;
    color: var(--slate);
  }
</style>
</head>
<body>
<main class="sign">
  <svg class="sign__bands" width="1200" height="600" viewBox="0 0 1200 600">
    <defs>
      <linearGradient id="forestFade" x1="0" y1="0" x2="0" y2="1">
        <stop offset="0" stop-color="#4f6b38" stop-opacity="0"/>
        <stop offset="1" stop-color="#5d7f3c" stop-opacity="0.9"/>
      </linearGradient>
    </defs>
    <rect class="band-top" x="0" y="0" width="1200" height="130" fill="#7dc242" role="img" aria-label="Row of pine tree silhouettes along the top band"/>
    <polygon class="panel-dark" points="0,131 1200,6 1200,480 0,600" fill="#20261f"/>
    <polygon class="forest-row" points="0,515 1200,360 1200,478 0,598" fill="url(#forestFade)" role="img" aria-label="Row of pine tree silhouettes rising above the bottom band"/>
    <polygon class="band-bottom" points="0,598 1200,475 1200,600 0,600" fill="#6ab245"/>
    <line class="rule-top" x1="0" y1="126" x2="1200" y2="3" stroke="#c5e88a" stroke-width="3"/>
    <line class="rule-bottom" x1="0" y1="593" x2="1200" y2="470" stroke="#c5e88a" stroke-width="3"/>
  </svg>

  <div class="brand__mark" aria-hidden="true"></div>
  <div class="brand">
    <div class="brand__name">Brookvale</div>
    <div class="brand__line">Building Company</div>
  </div>

  <h1 class="pitch pitch__headline">Build with the B-Crew!</h1>
  <div class="pitch pitch__phone">831 555 0172</div>
  <div class="pitch pitch__email">brookvalebuildingcompany@mailnest.example</div>
  <div class="pitch pitch__web">brookvalebuildingcompany.example</div>

  <div class="license">Lic# 4826130</div>
</main>
</body>
</html>
```